Halberd Guard Services

Our Company is a security business which needs a cut edge design, the final product should have all relevant information and maintain a bold but modern and professional look.

Target Market(s)

A cut edge design which will attract any audience

Industry/Entity Type

Security

Contact Information for Business Card

HALBERD GUARD SERVICES

Gregor Lindqvist
Operations Manager
Phone: 0491 735 219

Email: info@halberdguard.com.au
Web: www.halberdguard.com.au

Requirements
Must have
• Must be double sided and contain all relevant information and the company logo.

```html
<!DOCTYPE html>
<html lang="en">
<head>
<meta charset="utf-8">
<title>Halberd Guard Services – Business Card</title>
<link href="https://fonts.googleapis.com/css2?family=Arimo:wght@400;700&family=Open+Sans:wght@400;600&display=swap" rel="stylesheet">
<style>
  :root {
    --slate: #3f5a61;
    --orange: #f39a1c;
    --ink: #1f1f1f;
    --rule: #b9bcbe;
    --card: #ffffff;
    --backdrop: #e8e8e5;
  }
  * { box-sizing: border-box; margin: 0; padding: 0; }
  html, body { width: 1200px; height: 951px; overflow: hidden; }
  body {
    background: var(--backdrop);
    font-family: "Arimo", Arial, sans-serif;
    color: var(--ink);
    display: flex;
    flex-direction: column;
    align-items: center;
    justify-content: center;
    gap: 56px;
  }
  .card {
    position: relative;
    width: 700px;
    height: 400px;
    background: var(--card);
    border-radius: 26px;
    overflow: hidden;
    box-shadow: 0 6px 18px rgba(0,0,0,.18);
  }

  /* Front */
  .card-front {
    display: flex;
    flex-direction: column;
    align-items: center;
    justify-content: center;
  }
  .brand { display: flex; align-items: center; gap: 16px; }
  .brand-mark { width: 34px; height: 34px; background: var(--orange); flex: none; }
  .brand-name {
    font-weight: 700;
    color: var(--slate);
    letter-spacing: 1px;
    white-space: nowrap;
  }
  .card-front .brand-name { font-size: 54px; }
  .front-url {
    margin-top: 48px;
    font-family: "Open Sans", Arial, sans-serif;
    font-size: 22px;
    letter-spacing: 2px;
    color: var(--slate);
  }

  /* Back */
  .card-back .brand { position: absolute; left: 46px; top: 58px; gap: 10px; }
  .card-back .brand-mark { width: 20px; height: 20px; }
  .card-back .brand-name { font-size: 32px; }
  .person {
    position: absolute;
    right: 48px;
    top: 158px;
    display: flex;
    align-items: baseline;
    gap: 10px;
    white-space: nowrap;
  }
  .person-name { color: var(--orange); font-size: 25px; }
  .person-role { font-size: 19px; }
  .rule {
    position: absolute;
    left: 48px;
    right: 48px;
    top: 196px;
    height: 2px;
    background: var(--rule);
  }
  .contacts {
    position: absolute;
    left: 48px;
    right: 48px;
    top: 226px;
    display: flex;
    justify-content: space-between;
    font-size: 17px;
    font-weight: 700;
    line-height: 1.35;
  }
  .contact-group { display: flex; flex-direction: column; gap: 4px; }
  .contact-line { display: flex; align-items: flex-start; gap: 8px; white-space: nowrap; }
  .icon { width: 16px; height: 16px; flex: none; margin-top: 2px; fill: var(--orange); }
  .bands { position: absolute; left: 0; bottom: 0; width: 700px; height: 60px; }
</style>
</head>
<body>

  <section class="card card-front" aria-label="Card front">
    <div class="brand">
      <span class="brand-mark"></span>
      <span class="brand-name">HALBERD GUARD</span>
    </div>
    <p class="front-url">www.halberdguard.com.au</p>
  </section>

  <section class="card card-back" aria-label="Card back">
    <div class="brand">
      <span class="brand-mark"></span>
      <span class="brand-name">HALBERD GUARD</span>
    </div>

    <div class="person">
      <span class="person-name">Gregor Lindqvist</span>
      <span class="person-role">Operations Manager</span>
    </div>
    <div class="rule"></div>

    <div class="contacts">
      <div class="contact-group">
        <div class="contact-line">
          <svg class="icon" viewBox="0 0 16 16"><path d="M4 1c1 0 2 3 2 4s-1 1-1 2 3 4 4 4 1-1 2-1 4 1 4 2-2 3-3 3C6 15 1 10 1 4c0-1 2-3 3-3z"/></svg>
          <span>0491 735 219</span>
        </div>
      </div>
      <div class="contact-group">
        <div class="contact-line">
          <svg class="icon" viewBox="0 0 16 16"><path d="M1 3h14v10H1zm1 1 6 5 6-5z"/></svg>
          <span>info@halberdguard.com.au</span>
        </div>
        <div class="contact-line">
          <svg class="icon" viewBox="0 0 16 16"><circle cx="8" cy="8" r="7"/></svg>
          <span>www.halberdguard.com.au</span>
        </div>
      </div>
    </div>

    <svg class="bands" viewBox="0 0 700 60" preserveAspectRatio="none" aria-hidden="true">
      <polygon points="0,28 400,28 420,60 0,60" fill="var(--orange)"/>
      <polygon points="440,14 700,14 700,60 468,60" fill="var(--slate)"/>
    </svg>
  </section>

</body>
</html>
```